Graphic Design Project

A custom graphic explaining our business.

small urban farms are created, we then buy their products and take them to a distribution center, volunteers come and help us pack it into market baskets (make sure the volunteers reflect adults and kids), then those baskets are delivered to a drop off point where individuals come and pick them up.

It needs to be cute, friendly, and fun. Bright colors, maybe green. I am not a designer, so use your artistic judgment.

Target Market(s)

28-35 Family Friendly, global, diverse, socially counscious consumers

Industry/Entity Type

Business

Requirements
Must have
• This is a link for a custom graphic we made for another project.

http://www.pebblemeadowkites.com/wp-content/uploads/2010/09/Picture-46-1024x274.png

The image must fit into a rectangular window like the image shows in the link.
Nice to have
• Just make sure any people you place in the image reflect diversity, ages, races, etc. thanks.

```html
<!DOCTYPE html>
<html lang="en">
<head>
<meta charset="utf-8">
<title>From Urban Farms to Dropoff Point</title>
<link rel="stylesheet" href="https://fonts.googleapis.com/css2?family=Bebas+Neue&display=swap">
<style>
  :root {
    --orange: #fbad38;
    --ring: #999999;
    --ink: #111111;
    --paper: #ffffff;
  }
  html, body {
    margin: 0;
    padding: 0;
    width: 1200px;
    height: 600px;
    overflow: hidden;
    background: var(--paper);
  }
  .process {
    position: relative;
    width: 1200px;
    height: 600px;
  }
  .process__graphic {
    position: absolute;
    inset: 0;
  }
  .ring { fill: none; stroke: var(--ring); stroke-width: 9; }
  .flow { fill: none; stroke: var(--orange); stroke-width: 24; stroke-linejoin: miter; }
  .flow-head, .icon { fill: var(--orange); }
  .icon-line { stroke: var(--orange); fill: none; }
  .volunteers { fill: var(--orange); }
  .step-label {
    position: absolute;
    width: 260px;
    margin: 0;
    text-align: center;
    font-family: "Bebas Neue", "Oswald", sans-serif;
    font-weight: 400;
    color: var(--ink);
    line-height: 0.92;
    text-shadow: 3px 3px 0 var(--orange);
    letter-spacing: 1px;
  }
  .step-label span { display: block; }
  .step-label--farms { left: 20px; top: 440px; font-size: 56px; }
  .step-label--center { left: 323px; top: 440px; }
  .step-label--center .small { font-size: 30px; }
  .step-label--center .large { font-size: 50px; }
  .step-label--packing { left: 620px; top: 440px; }
  .step-label--packing .small { font-size: 42px; }
  .step-label--packing .large { font-size: 54px; }
  .step-label--point { left: 920px; top: 440px; }
  .step-label--point .small { font-size: 40px; }
  .step-label--point .large { font-size: 54px; }
</style>
</head>
<body>
<main class="process">
  <svg class="process__graphic" width="1200" height="600" viewBox="0 0 1200 600" aria-hidden="false">
    <defs>
      <g id="basket">
        <rect x="-52" y="-22" width="104" height="9"/>
        <rect x="-48" y="-2" width="96" height="9"/>
        <rect x="-44" y="18" width="88" height="9"/>
        <rect x="-36" y="-26" width="8" height="62"/>
        <rect x="-16" y="-26" width="8" height="62"/>
        <rect x="8" y="-26" width="8" height="62"/>
        <rect x="28" y="-26" width="8" height="62"/>
        <polygon points="-14,-48 -8,-54 16,-28 10,-22"/>
      </g>
    </defs>

    <!-- flow arrows -->
    <polyline class="flow" points="142,112 212,45 393,45 462,114"/>
    <polygon class="flow-head" points="445,134 484,136 481,96"/>

    <polyline class="flow" points="580,240 625,198 655,198"/>
    <polygon class="flow-head" points="652,178 676,198 652,218"/>
    <polyline class="flow" points="580,290 625,330 655,330"/>
    <polygon class="flow-head" points="652,310 676,330 652,350"/>

    <polyline class="flow" points="822,198 856,198 890,232"/>
    <polygon class="flow-head" points="872,247 922,240 908,206"/>
    <polyline class="flow" points="822,330 856,330 890,296"/>
    <polygon class="flow-head" points="872,281 922,288 908,322"/>

    <line class="flow" x1="988" y1="150" x2="962" y2="104"/>
    <polygon class="flow-head" points="942,68 980,96 946,114"/>
    <line class="flow" x1="1048" y1="136" x2="1048" y2="74"/>
    <polygon class="flow-head" points="1030,76 1048,42 1066,76"/>
    <line class="flow" x1="1108" y1="150" x2="1134" y2="104"/>
    <polygon class="flow-head" points="1154,68 1116,96 1150,114"/>

    <!-- rings -->
    <circle class="ring" cx="150" cy="260" r="118"/>
    <circle class="ring" cx="453" cy="262" r="118"/>
    <circle class="ring" cx="740" cy="198" r="58"/>
    <circle class="ring" cx="740" cy="330" r="58"/>
    <circle class="ring" cx="1050" cy="262" r="118"/>

    <!-- wheat -->
    <g class="icon wheat">
      <rect x="148" y="178" width="4" height="180"/>
      <ellipse cx="150" cy="185" rx="7" ry="16"/>
      <g transform="translate(150 215)">
        <ellipse cx="-13" cy="0" rx="7" ry="15" transform="rotate(-35 -13 0)"/>
        <ellipse cx="13" cy="0" rx="7" ry="15" transform="rotate(35 13 0)"/>
      </g>
      <g transform="translate(150 245)">
        <ellipse cx="-13" cy="0" rx="7" ry="15" transform="rotate(-35 -13 0)"/>
        <ellipse cx="13" cy="0" rx="7" ry="15" transform="rotate(35 13 0)"/>
      </g>
      <g transform="translate(150 275)">
        <ellipse cx="-13" cy="0" rx="7" ry="15" transform="rotate(-35 -13 0)"/>
        <ellipse cx="13" cy="0" rx="7" ry="15" transform="rotate(35 13 0)"/>
      </g>
      <g transform="translate(150 305)">
        <ellipse cx="-13" cy="0" rx="7" ry="15" transform="rotate(-35 -13 0)"/>
        <ellipse cx="13" cy="0" rx="7" ry="15" transform="rotate(35 13 0)"/>
      </g>
    </g>

    <!-- open box -->
    <g class="icon box">
      <polygon points="336,188 392,184 452,238 392,262"/>
      <polygon points="570,188 514,184 454,238 514,262"/>
      <polygon points="390,270 452,246 516,270 454,294"/>
      <polygon points="390,278 450,300 450,358 390,334"/>
      <polygon points="516,278 456,300 456,358 516,334"/>
    </g>

    <!-- baskets -->
    <use class="icon" href="#basket" transform="translate(740 205)"/>
    <use class="icon" href="#basket" transform="translate(740 337)"/>
    <use class="icon" href="#basket" transform="translate(1050 262) scale(1.3)"/>

    <!-- volunteers -->
    <rect class="volunteers" x="700" y="30" width="84" height="102" rx="6" role="img" aria-label="Silhouettes of volunteers: two adults and a child waving"/>
  </svg>

  <h2 class="step-label step-label--farms"><span>Urban</span><span>Farms</span></h2>
  <h2 class="step-label step-label--center"><span class="small">Distribution</span><span class="large">Center</span></h2>
  <h2 class="step-label step-label--packing"><span class="small">Volunteer</span><span class="large">Packing</span></h2>
  <h2 class="step-label step-label--point"><span class="small">Dropoff</span><span class="large">Point</span></h2>
</main>
</body>
</html>
```